Business Card Design

New business card design

Target Market(s)

Residential & Commercial Property Managers

Industry/Entity Type

Plumbing Services

Contact Information for Business Card

Name - Rowan Keddle, title - Director, Phone Number - 0431 286 517, email - rowan@tbk-plumbing.com.au, Company ABN - 73 215 904 386,

Font styles to use
Sans Serif

Colors
0054AA
0677BA
7BADD7
CADEEF
E8F1F8

```html
<!DOCTYPE html>
<html lang="en">
<head>
<meta charset="utf-8">
<title>TBK Plumbing Services – Business Card</title>
<link rel="stylesheet" href="https://fonts.googleapis.com/css2?family=Roboto:wght@300;400&family=Michroma&display=swap">
<style>
  :root {
    --backdrop: #2f3033;
    --card: #1f242b;
    --accent: #18a6ea;
    --ink: #ffffff;
    --ink-soft: #d9dde2;
  }
  * { box-sizing: border-box; margin: 0; padding: 0; }
  html, body { width: 1200px; height: 689px; overflow: hidden; }
  body {
    background: var(--backdrop);
    font-family: "Roboto", Arial, sans-serif;
    color: var(--ink);
    position: relative;
  }
  .card {
    position: absolute;
    top: 195px;
    width: 520px;
    height: 300px;
    background: var(--card);
    border-radius: 24px;
    border-left: 4px solid var(--accent);
    border-bottom: 4px solid var(--accent);
    overflow: hidden;
  }
  .card--front { left: 50px; }
  .card--back { left: 630px; }

  .wordmark { display: flex; align-items: center; gap: 10px; }
  .wordmark__dot {
    width: 14px; height: 14px; border-radius: 50%;
    background: var(--accent);
  }
  .wordmark__name {
    font-weight: 300;
    color: var(--ink);
    white-space: nowrap;
  }
  .card--front .wordmark {
    position: absolute; left: 0; right: 0; top: 118px;
    justify-content: center;
  }
  .card--front .wordmark__name { font-size: 40px; letter-spacing: 2px; }

  .corner-dot {
    position: absolute; top: 28px; right: -22px;
    width: 44px; height: 44px; border-radius: 50%;
    background: var(--accent);
  }
  .person {
    position: absolute; top: 40px; right: 40px; text-align: right;
  }
  .person__name {
    font-family: "Michroma", Arial, sans-serif;
    font-size: 17px; letter-spacing: 1px; color: var(--ink);
  }
  .person__title {
    font-size: 15px; color: var(--accent); margin-top: 2px;
  }
  .card--back .wordmark { position: absolute; left: 38px; top: 118px; }
  .card--back .wordmark__dot { width: 10px; height: 10px; }
  .card--back .wordmark__name { font-size: 26px; letter-spacing: 1.5px; }

  .contact {
    position: absolute; left: 38px; bottom: 36px;
    font-size: 15px; line-height: 1.45; color: var(--ink-soft);
    list-style: none;
  }
  .contact li { display: flex; align-items: center; gap: 8px; }
  .contact svg { width: 14px; height: 14px; fill: var(--accent); flex: none; }
  .contact__abn { margin-top: 6px; }
</style>
</head>
<body>
  <section class="card card--front" aria-label="Card front">
    <div class="wordmark">
      <span class="wordmark__name">tbk plumbing services</span>
      <span class="wordmark__dot"></span>
    </div>
  </section>

  <section class="card card--back" aria-label="Card back">
    <span class="corner-dot"></span>
    <div class="person">
      <p class="person__name">ROWAN KEDDLE</p>
      <p class="person__title">Director</p>
    </div>
    <div class="wordmark">
      <span class="wordmark__name">tbk plumbing services</span>
      <span class="wordmark__dot"></span>
    </div>
    <ul class="contact">
      <li>
        <svg viewBox="0 0 24 24" aria-hidden="true"><path d="M6.6 10.8a15 15 0 0 0 6.6 6.6l2.2-2.2a1 1 0 0 1 1-.25 11.4 11.4 0 0 0 3.6.57 1 1 0 0 1 1 1V20a1 1 0 0 1-1 1A17 17 0 0 1 3 4a1 1 0 0 1 1-1h3.5a1 1 0 0 1 1 1c0 1.25.2 2.45.57 3.6a1 1 0 0 1-.25 1z"/></svg>
        0431 286 517
      </li>
      <li>
        <svg viewBox="0 0 24 24" aria-hidden="true"><path d="M2 5h20v14H2zm2 2v.4l8 5.2 8-5.2V7zm0 2.8V17h16V9.8l-8 5.2z"/></svg>
        rowan@tbk-plumbing.com.au
      </li>
      <li class="contact__abn">Company ABN - 73 215 904 386</li>
    </ul>
  </section>
</body>
</html>
```